Ridgeline Journeys business card

please see website
www.ridgelinejourneys.comau

info needed on card
Curtis Halvey
Ph
email
Adventure Riding GPS trails

please use my logo and colours off my site

Curtis Halvey
curtis@ridgelinejourneys.com

```html
<!DOCTYPE html>
<html lang="en">
<head>
<meta charset="utf-8">
<title>Ridgeline Journeys business card</title>
<link href="https://fonts.googleapis.com/css2?family=Open+Sans:wght@400;700&display=swap" rel="stylesheet">
<style>
  :root {
    --canvas-bg: #c8c8c8;
    --ink: #1a1a1a;
    --mark-grey: #5a5a5a;
    --brand-yellow: #f0dc1e;
    --band-black: #080808;
    --light-text: #ececec;
    --card-front-top: #f3f3f3;
    --card-front-bottom: #d4d4d4;
    --card-back-glow: #fbfbf2;
    --card-back-yellow: #d8cf2c;
  }
  * { box-sizing: border-box; margin: 0; padding: 0; }
  html, body {
    width: 1189px; height: 1200px; overflow: hidden;
    background: var(--canvas-bg);
    font-family: "Open Sans", Arial, sans-serif;
  }
  .card {
    position: absolute; left: 140px; width: 918px; height: 524px;
    overflow: hidden;
    box-shadow: 0 6px 14px rgba(0,0,0,0.35);
  }
  .card-front {
    top: 45px;
    background: linear-gradient(180deg, var(--card-front-top), var(--card-front-bottom) 70%);
  }
  .card-back {
    top: 623px;
    background: radial-gradient(ellipse 90% 75% at 50% 0%, var(--card-back-glow) 0%, #eeeaa8 45%, var(--card-back-yellow) 100%);
  }
  .wave { position: absolute; inset: 0; width: 100%; height: 100%; }
  .brand-dot {
    position: absolute; border-radius: 50%; background: var(--mark-grey);
  }
  .brand-name {
    position: absolute; color: var(--ink); font-weight: 700;
    font-size: 64px; line-height: 70px; letter-spacing: 0.5px;
  }
  .person-name {
    position: absolute; left: 56px; top: 382px;
    color: var(--light-text); font-size: 47px; font-weight: 400;
    white-space: nowrap;
  }
  .divider {
    position: absolute; left: 394px; top: 368px; width: 4px; height: 132px;
    background: var(--light-text);
  }
  .contact {
    position: absolute; left: 424px; display: flex; align-items: center; gap: 22px;
    color: var(--light-text); font-size: 26px; white-space: nowrap;
  }
  .contact svg { width: 24px; height: 24px; flex: none; }
  .contact-email { top: 406px; }
  .contact-web { top: 449px; }
</style>
</head>
<body>

<section class="card card-front">
  <svg class="wave" viewBox="0 0 1124 642" preserveAspectRatio="none" aria-hidden="true">
    <path fill="var(--brand-yellow)" d="M0,340 C200,400 400,420 560,395 C700,372 780,332 880,332 C980,334 1060,370 1124,400 L1124,642 L0,642 Z"/>
    <path fill="var(--band-black)" d="M0,412 C200,452 400,452 560,418 C700,385 790,332 880,332 C980,334 1060,370 1124,400 L1124,642 L0,642 Z"/>
  </svg>

  <div class="brand-dot" style="left:180px; top:50px; width:180px; height:180px;"></div>
  <div class="brand-name" style="left:400px; top:75px;">Ridgeline<br>Journeys</div>

  <div class="person-name">Curtis Halvey</div>
  <div class="divider"></div>

  <div class="contact contact-email">
    <svg viewBox="0 0 24 24" aria-hidden="true">
      <rect x="1" y="3" width="22" height="18" fill="var(--light-text)"/>
      <rect x="5" y="7" width="14" height="10" fill="none" stroke="var(--band-black)" stroke-width="1.6"/>
      <path d="M5,7 L12,13 L19,7" fill="none" stroke="var(--band-black)" stroke-width="1.6"/>
    </svg>
    <span>curtis@ridgelinejourneys.com</span>
  </div>
  <div class="contact contact-web">
    <svg viewBox="0 0 24 24" aria-hidden="true">
      <rect x="1" y="1" width="22" height="22" fill="var(--light-text)"/>
      <circle cx="12" cy="12" r="7" fill="none" stroke="var(--band-black)" stroke-width="1.6"/>
      <path d="M5,12 H19 M12,5 C8,9 8,15 12,19 M12,5 C16,9 16,15 12,19" fill="none" stroke="var(--band-black)" stroke-width="1.3"/>
    </svg>
    <span>www.ridgelinejourneys.com.au</span>
  </div>
</section>

<section class="card card-back">
  <div class="brand-dot" style="left:168px; top:172px; width:196px; height:196px;"></div>
  <div class="brand-name" style="left:404px; top:200px;">Ridgeline<br>Journeys</div>
</section>

</body>
</html>
```